Social Health & Parkinson's

I need a 1-pg horizontal infographic that can be handed out to patients and providers. It needs to be scientifically sound (data provided), easy to understand, and visually pleasing. Target audience; patiens (mostly 40-90 years old) and providers (neurologists, nurses, physical therapists, naturopathic physicians, support group leaders, etc.) We need 6 of these, one for each topic listed on the website. Ideally, we'll hire the winner for 5 more similar projects and keep a theme.

Target Market(s)

Patients with Parkinson's disease, their families, care providers. To be handed out by physicians, support group leaders, etc.

Colors

Designer to choose colors to be used in the design.

Requirements
Must have
• Visually stunning. Data integrity-- keep the numbers and the figures we provide. Reference to where the data is coming from. Be thoughtful of elderly, vision issues. Teach everyone something.

```html
<!DOCTYPE html>
<html lang="en">
<head>
<meta charset="utf-8">
<title>Social Health &amp; Patient-Reported Outcomes in PD</title>
<link href="https://fonts.googleapis.com/css2?family=Bebas+Neue&family=Figtree:wght@400;500;600;700&display=swap" rel="stylesheet">
<style>
  :root{
    --blue:#86b7dc;
    --blue-text:#5b9dd3;
    --peach:#fdcba5;
    --peach-light:#fde3d3;
    --lavender:#c6d1ec;
    --green:#dcf2d1;
    --pink:#e6a6c2;
    --orange:#f5a36f;
    --ink:#1f1f1f;
    --panel:#ebebeb;
    --page:#ffffff;
    --gutter:#e8e8e8;
  }
  *{margin:0;padding:0;box-sizing:border-box}
  html,body{width:1200px;height:936px;overflow:hidden;background:var(--page)}
  body{font-family:"Figtree",Arial,sans-serif;color:var(--ink)}
  .poster{position:relative;width:1200px;height:936px;overflow:hidden;background:var(--page)}
  .layer{position:absolute;left:0;top:0}
  .tagline{position:absolute;left:336px;top:53px;color:#fff;font-size:17px;letter-spacing:3.2px;font-weight:500;white-space:nowrap}
  .title{position:absolute;left:330px;top:82px;width:850px;color:#fff;font-family:"Bebas Neue",Impact,sans-serif;font-size:52px;line-height:1;letter-spacing:.2px;white-space:nowrap}
  .partner{position:absolute;left:18px;display:flex;align-items:center;gap:8px;color:#fff;font-size:13px;font-weight:600}
  .partner::before{content:"";width:14px;height:14px;border-radius:50%;background:#fff;flex:none}
  .partner--first{top:100px}
  .partner--second{top:128px}
  .finding{position:absolute;background:var(--panel);font-size:11.6px;line-height:1.42;text-align:justify;box-shadow:0 7px 6px -5px rgba(0,0,0,.22)}
  .finding--summary{left:0;top:434px;width:333px;height:55px;border-radius:0 28px 28px 0;padding:8px 16px 0 22px;font-size:14.6px;line-height:1.3;text-align:left}
  .finding--side{left:897px;width:303px;border-radius:24px 0 0 24px;padding:8px 22px 0 12px}
  .footer-text{position:absolute;left:0;top:902px;width:1200px;text-align:center;color:#fff;font-size:17px;letter-spacing:2.6px;font-weight:500}
  svg text{font-family:"Figtree",Arial,sans-serif}
  .chart-title{fill:var(--blue-text);font-size:13px;font-weight:500}
  .chart-subtitle{fill:var(--blue-text);font-size:10.4px;font-weight:500}
  .axis-label{fill:var(--ink);font-size:8px}
  .axis-title{fill:var(--ink);font-size:8.4px;font-weight:500}
  .tick{fill:var(--ink);font-size:8px}
  .small{fill:var(--ink);font-size:5.4px}
  .row-label{fill:var(--ink);font-size:8px;font-weight:500}
  .tag-label{fill:#fff;font-size:9.6px;font-weight:700;letter-spacing:.6px}
</style>
</head>
<body>
<main class="poster">

  <!-- header -->
  <svg class="layer header-art" width="1200" height="175" viewBox="0 0 1200 175">
    <rect x="0" y="32" width="1200" height="18" fill="var(--blue)"/>
    <rect x="0" y="50" width="1200" height="27" fill="var(--peach)"/>
    <path d="M0 77 H272 V130 Q272 172 230 172 H0 Z" fill="var(--blue)"/>
    <path d="M299 172 V110 Q299 77 334 77 H1200 V172 Z" fill="var(--blue)"/>
    <path d="M286 37 L316 77 L299 77 L299 172 L272 172 L272 77 L256 77 Z" fill="#fff"/>
    <line x1="286" y1="6" x2="286" y2="37" stroke="#333" stroke-width="1.6"/>
    <rect x="286" y="6" width="18" height="14" fill="#e08159"/>
    <path d="M296 10 H311 L306 15 L311 20 H296 Z" fill="#ea6a2e"/>
  </svg>
  <div class="tagline">Rx: Nurture social health &nbsp;●&nbsp; Make friends &nbsp;●&nbsp; Avoid loneliness.</div>
  <h1 class="title">SOCIAL HEALTH &amp; PATIENT - REPORTED OUTCOMES IN PD</h1>
  <div class="partner partner--first">Cedar Ridge University</div>
  <div class="partner partner--second">Northfield PD Network</div>

  <!-- charts -->
  <svg class="layer charts" width="1200" height="936" viewBox="0 0 1200 936">
    <!-- column gutters & lower right panel -->
    <rect x="356" y="172" width="2" height="717" fill="var(--gutter)"/>
    <rect x="872" y="172" width="2" height="458" fill="var(--gutter)"/>
    <rect x="874" y="630" width="326" height="259" fill="#f1f1f1"/>

    <!-- correlation chart -->
    <g class="chart chart--correlation">
      <text class="chart-title" x="249" y="211" text-anchor="middle">Correlation Between</text>
      <text class="chart-title" x="249" y="227" text-anchor="middle">Quality of Life and PRO-PD Score</text>
      <rect x="22" y="235" width="18" height="155" fill="var(--ink)"/>
      <text class="tag-label" transform="translate(34 312) rotate(-90)" text-anchor="middle">PRO-PD Score</text>
      <rect x="70" y="235" width="194" height="61" fill="var(--peach)"/>
      <rect x="70" y="296" width="194" height="31" fill="var(--peach-light)"/>
      <rect x="70" y="327" width="194" height="30" fill="var(--lavender)"/>
      <rect x="70" y="357" width="194" height="31" fill="var(--green)"/>
      <rect x="283" y="235" width="50" height="61" fill="var(--peach)"/>
      <rect x="283" y="296" width="50" height="31" fill="var(--peach-light)"/>
      <rect x="283" y="327" width="50" height="30" fill="var(--lavender)"/>
      <rect x="283" y="357" width="50" height="31" fill="var(--green)"/>
      <text class="axis-label" x="308" y="271" text-anchor="middle" font-size="9">Poor</text>
      <text class="axis-label" x="308" y="315" text-anchor="middle" font-size="9">*Fair</text>
      <text class="axis-label" x="308" y="345" text-anchor="middle" font-size="9">Good</text>
      <text class="axis-label" x="308" y="376" text-anchor="middle" font-size="9" font-weight="600">Excellent</text>
      <text transform="translate(278 326) rotate(-90)" text-anchor="middle" fill="var(--blue-text)" font-size="11" font-weight="700" letter-spacing=".6">Quality of Life</text>
      <line x1="70" y1="351" x2="296" y2="284" stroke="#111" stroke-width="0.8"/>
      <g class="tick" text-anchor="end">
        <text x="62" y="242">2500</text><text x="62" y="272">2000</text><text x="62" y="302">1500</text>
        <text x="62" y="331">1000</text><text x="62" y="361">500</text><text x="62" y="391">0</text>
      </g>
      <g class="tick" text-anchor="middle">
        <text x="109" y="401">5</text><text x="147" y="401">10</text><text x="184" y="401">15</text>
        <text x="220" y="401">20</text><text x="258" y="401">25</text><text x="296" y="401">30</text><text x="333" y="401">35</text>
      </g>
      <text class="axis-title" x="200" y="417" text-anchor="middle">Years Since Diagnosis</text>
    </g>

    <!-- social satisfaction chart -->
    <g class="chart chart--satisfaction">
      <text class="chart-subtitle" x="208" y="522" text-anchor="middle">In general, please rate how well you rate your satisfaction with</text>
      <text class="chart-subtitle" x="208" y="534" text-anchor="middle">your social activities and relationships</text>
      <rect x="22" y="548" width="18" height="92" fill="var(--ink)"/>
      <text class="tag-label" transform="translate(34 594) rotate(-90)" text-anchor="middle">PRO-PD</text>
      <g class="tick" text-anchor="end">
        <text x="80" y="558">2000</text><text x="80" y="579">1500</text><text x="80" y="600">1000</text>
        <text x="80" y="620">500</text><text x="80" y="641">0</text>
      </g>
      <line x1="87" y1="550" x2="87" y2="638" stroke="#999" stroke-width=".6"/>
      <line x1="87" y1="638" x2="327" y2="638" stroke="#999" stroke-width=".6"/>
      <path d="M327 635 L333 638 L327 641 Z" fill="#999"/>
      <rect x="104" y="617.5" width="22" height="20.5" fill="var(--green)"/>
      <rect x="149" y="610.3" width="22" height="27.7" fill="var(--pink)"/>
      <rect x="193" y="601.1" width="22" height="36.9" fill="var(--lavender)"/>
      <rect x="237" y="589.1" width="22" height="48.9" fill="var(--peach-light)"/>
      <rect x="282" y="583.3" width="22" height="54.7" fill="var(--peach)"/>
      <g class="small" text-anchor="middle">
        <text x="115" y="614">494</text><text x="160" y="607">667</text><text x="204" y="598">889</text>
        <text x="248" y="586">1178</text><text x="293" y="580">1317</text>
        <text x="115" y="648">Excellent</text><text x="115" y="655">(n=343)</text>
        <text x="160" y="648">Very Good</text><text x="160" y="655">(n=607)</text>
        <text x="204" y="648">Good</text><text x="204" y="655">(n=468)</text>
        <text x="248" y="648">Fair</text><text x="248" y="655">(n=268)</text>
        <text x="293" y="648">Poor</text><text x="293" y="655">(n=61)</text>
        <text x="208" y="676" font-size="6">Social Satisfaction</text>
      </g>
    </g>

    <!-- social roles chart -->
    <g class="chart chart--roles">
      <text class="chart-subtitle" x="208" y="716" text-anchor="middle">In general, please rate how well you carry out</text>
      <text class="chart-subtitle" x="208" y="728" text-anchor="middle">your social activities and roles</text>
      <rect x="22" y="742" width="18" height="92" fill="var(--ink)"/>
      <text class="tag-label" transform="translate(34 788) rotate(-90)" text-anchor="middle">PRO-PD</text>
      <g class="tick" text-anchor="end">
        <text x="80" y="753">2000</text><text x="80" y="774">1500</text><text x="80" y="795">1000</text>
        <text x="80" y="815">500</text><text x="80" y="836">0</text>
      </g>
      <line x1="87" y1="745" x2="87" y2="833" stroke="#999" stroke-width=".6"/>
      <line x1="87" y1="833" x2="327" y2="833" stroke="#999" stroke-width=".6"/>
      <path d="M327 830 L333 833 L327 836 Z" fill="#999"/>
      <rect x="104" y="814.5" width="22" height="18.5" fill="var(--green)"/>
      <rect x="149" y="805.9" width="22" height="27.1" fill="var(--pink)"/>
      <rect x="193" y="791.8" width="22" height="41.2" fill="var(--lavender)"/>
      <rect x="237" y="781.8" width="22" height="51.2" fill="var(--peach-light)"/>
      <rect x="282" y="772.2" width="22" height="60.8" fill="var(--peach)"/>
      <g class="small" text-anchor="middle">
        <text x="115" y="811">446</text><text x="160" y="802">653</text><text x="204" y="788">992</text>
        <text x="248" y="778">1233</text><text x="293" y="769">1464</text>
        <text x="115" y="843">Excellent</text><text x="115" y="850">(n=322)</text>
        <text x="160" y="843">Very Good</text><text x="160" y="850">(n=647)</text>
        <text x="204" y="843">Good</text><text x="204" y="850">(n=491)</text>
        <text x="248" y="843">Fair</text><text x="248" y="850">(n=247)</text>
        <text x="293" y="843">Poor</text><text x="293" y="850">(n=44)</text>
        <text x="208" y="870" font-size="6">Social Satisfaction</text>
      </g>
    </g>

    <!-- modifiable variables chart -->
    <g class="chart chart--variables">
      <text class="chart-title" x="640" y="211" text-anchor="middle">Modifiable variables associated with</text>
      <text class="chart-title" x="640" y="227" text-anchor="middle">risk of parkinsons disease</text>
      <g stroke="#e2e2e2" stroke-width=".8">
        <line x1="507" y1="242" x2="507" y2="453"/><line x1="551" y1="242" x2="551" y2="453"/>
        <line x1="595" y1="242" x2="595" y2="453"/><line x1="639" y1="242" x2="639" y2="453"/>
        <line x1="683" y1="242" x2="683" y2="453"/><line x1="727" y1="242" x2="727" y2="453"/>
        <line x1="771" y1="242" x2="771" y2="453"/><line x1="815" y1="242" x2="815" y2="453"/>
        <line x1="859" y1="242" x2="859" y2="453"/>
      </g>
      <g class="row-label">
        <text x="387" y="251">Exercise 30+ min/d, 7 days/wk</text>
        <text x="387" y="270.6">Exercise 30+ min/d, 6 days/wk</text>
        <text x="387" y="290.2">Exercise 30+ min/d, 5 days/wk</text>
        <text x="387" y="309.8">Exercise 30+ min/d, 4 days/wk</text>
        <text x="387" y="329.4">Exercise 30+ min/d, 3 days/wk</text>
        <text x="387" y="349">I have lots of friends</text>
        <text x="387" y="368.6">I cook most of my meals</text>
        <text x="387" y="388.2">I practice stress management</text>
        <text x="387" y="407.8">I am overweight</text>
        <text x="387" y="427.4">I have a lot of stress</text>
        <text x="387" y="447">I am lonely</text>
      </g>
      <g fill="var(--peach)">
        <rect x="550.6" y="244.8" width="132.4" height="6.4"/>
        <rect x="554.5" y="264.4" width="128.5" height="6.4"/>
        <rect x="578.7" y="284" width="104.3" height="6.4"/>
        <rect x="582.2" y="303.6" width="100.8" height="6.4"/>
        <rect x="598.5" y="323.2" width="84.5" height="6.4"/>
        <rect x="609.1" y="342.8" width="73.9" height="6.4"/>
        <rect x="618.8" y="362.4" width="64.2" height="6.4"/>
        <rect x="662.8" y="382" width="20.2" height="6.4"/>
      </g>
      <rect x="683" y="401.6" width="61.2" height="6.4" fill="var(--lavender)"/>
      <rect x="683" y="421.2" width="79.2" height="6.4" fill="var(--green)"/>
      <rect x="683" y="440.8" width="144.3" height="6.4" fill="var(--pink)"/>
      <g class="small" font-size="6">
        <text x="688" y="250.5">-301</text><text x="688" y="270">-292</text><text x="688" y="289.6">-237</text>
        <text x="688" y="309.2">-229</text><text x="688" y="328.8">-192</text><text x="688" y="348.4">-168</text>
        <text x="688" y="368">-146</text><text x="688" y="387.6">-46</text>
      </g>
      <g class="small" font-size="6" text-anchor="end">
        <text x="673" y="407.2">139</text><text x="673" y="426.8">180</text><text x="673" y="446.4">328</text>
      </g>
      <g class="tick" text-anchor="middle">
        <text x="507" y="467">-400</text><text x="551" y="467">-300</text><text x="595" y="467">-200</text>
        <text x="639" y="467">-100</text><text x="683" y="467">0</text><text x="727" y="467">100</text>
        <text x="771" y="467">200</text><text x="815" y="467">300</text><text x="859" y="467">400</text>
      </g>
    </g>

    <!-- quality of life vs tremor -->
    <g class="chart chart--tremor">
      <text class="chart-title" x="511" y="570" text-anchor="middle">Quality of Life vs. Tremor</text>
      <rect x="376" y="578" width="18" height="144" fill="var(--ink)"/>
      <text transform="translate(388 650) rotate(-90)" text-anchor="middle" fill="#fff" font-size="7.6" font-weight="700">PROMIS Total-Quality of Life</text>
      <g stroke="#fbd5bb" stroke-width=".8">
        <line x1="418" y1="583" x2="605" y2="583"/><line x1="418" y1="604.3" x2="605" y2="604.3"/>
        <line x1="418" y1="625.7" x2="605" y2="625.7"/><line x1="418" y1="647" x2="605" y2="647"/>
        <line x1="418" y1="668.3" x2="605" y2="668.3"/><line x1="418" y1="689.7" x2="605" y2="689.7"/>
        <line x1="455.4" y1="583" x2="455.4" y2="711"/><line x1="492.8" y1="583" x2="492.8" y2="711"/>
        <line x1="530.2" y1="583" x2="530.2" y2="711"/><line x1="567.6" y1="583" x2="567.6" y2="711"/>
        <line x1="605" y1="583" x2="605" y2="711"/>
      </g>
      <line x1="418" y1="583" x2="418" y2="711" stroke="#f5b58b" stroke-width=".8"/>
      <line x1="418" y1="711" x2="605" y2="711" stroke="#f5b58b" stroke-width=".8"/>
      <line x1="418" y1="625.7" x2="605" y2="647" stroke="#111" stroke-width="2" stroke-dasharray="1.6 2.2" stroke-linecap="round"/>
      <text class="small" x="601" y="594" text-anchor="end">R² = 0.0754</text>
      <g class="tick" text-anchor="end">
        <text x="412" y="586">60</text><text x="412" y="607">50</text><text x="412" y="628">40</text>
        <text x="412" y="650">30</text><text x="412" y="671">20</text><text x="412" y="692">10</text><text x="412" y="714">0</text>
      </g>
      <g class="tick" text-anchor="middle">
        <text x="420" y="725">0</text><text x="455.4" y="725">20</text><text x="492.8" y="725">40</text>
        <text x="530.2" y="725">60</text><text x="567.6" y="725">80</text><text x="603" y="725">100</text>
      </g>
      <text class="axis-title" x="511" y="739" text-anchor="middle">Tremor</text>
    </g>

    <!-- quality of life vs withdrawn -->
    <g class="chart chart--withdrawn">
      <text class="chart-title" x="759" y="570" text-anchor="middle">Quality of Life vs. Withdrawn</text>
      <rect x="624" y="578" width="18" height="144" fill="var(--ink)"/>
      <text transform="translate(636 650) rotate(-90)" text-anchor="middle" fill="#fff" font-size="7.6" font-weight="700">PROMIS Total-Quality of Life</text>
      <g stroke="#fbd5bb" stroke-width=".8">
        <line x1="665" y1="604.3" x2="853" y2="604.3"/><line x1="665" y1="625.7" x2="853" y2="625.7"/>
        <line x1="665" y1="647" x2="853" y2="647"/><line x1="665" y1="668.3" x2="853" y2="668.3"/>
        <line x1="665" y1="689.7" x2="853" y2="689.7"/>
        <line x1="702.6" y1="583" x2="702.6" y2="711"/><line x1="740.2" y1="583" x2="740.2" y2="711"/>
        <line x1="777.8" y1="583" x2="777.8" y2="711"/><line x1="815.4" y1="583" x2="815.4" y2="711"/>
      </g>
      <rect x="665" y="583" width="188" height="128" fill="none" stroke="var(--orange)" stroke-width="1"/>
      <line x1="665" y1="625.7" x2="853" y2="668.3" stroke="#111" stroke-width="2" stroke-dasharray="1.6 2.2" stroke-linecap="round"/>
      <text class="small" x="849" y="594" text-anchor="end">R² = 0.4872</text>
      <g class="tick" text-anchor="end">
        <text x="659" y="586">60</text><text x="659" y="607">50</text><text x="659" y="628">40</text>
        <text x="659" y="650">30</text><text x="659" y="671">20</text><text x="659" y="692">10</text><text x="659" y="714">0</text>
      </g>
      <g class="tick" text-anchor="middle">
        <text x="667" y="725">0</text><text x="702.6" y="725">20</text><text x="740.2" y="725">40</text>
        <text x="777.8" y="725">60</text><text x="815.4" y="725">80</text><text x="851" y="725">100</text>
      </g>
      <text class="axis-title" x="755" y="739" text-anchor="middle">Withdrawn</text>
    </g>

    <!-- illustration area -->
    <defs>
      <linearGradient id="careFill" x1="0" y1="0" x2="0" y2="1">
        <stop offset="0" stop-color="#9cc6e6"/>
        <stop offset="1" stop-color="#7fb2da"/>
      </linearGradient>
    </defs>
    <path role="img" aria-label="Illustration of two open hands cradling a brain" d="M545 800 Q545 760 590 757 Q626 752 660 757 Q708 762 708 800 L708 889 H545 Z" fill="url(#careFill)"/>

    <!-- average PRO-PD by years -->
    <g class="chart chart--years">
      <text class="chart-title" x="1034" y="212" text-anchor="middle" font-size="11.4">Average PRO-PD by Years  Since Diganosis</text>
      <rect x="887" y="253" width="19" height="92" fill="var(--ink)"/>
      <text class="tag-label" transform="translate(900 299) rotate(-90)" text-anchor="middle">PRO-PD</text>
      <line x1="952" y1="229" x2="952" y2="377" stroke="#999" stroke-width=".6"/>
      <line x1="952" y1="377" x2="1177" y2="377" stroke="#999" stroke-width=".6"/>
      <path d="M1176 374 L1183 377 L1176 380 Z" fill="#999"/>
      <g class="tick" text-anchor="end">
        <text x="946" y="232">1400</text><text x="946" y="253">1200</text><text x="946" y="274">1000</text>
        <text x="946" y="295">800</text><text x="946" y="316">600</text><text x="946" y="337">400</text>
        <text x="946" y="359">200</text><text x="946" y="380">0</text>
      </g>
      <g class="small" font-size="6" text-anchor="middle">
        <text x="960" y="390">0</text><text x="980.2" y="390">1</text><text x="1000.4" y="390">2</text>
        <text x="1020.6" y="390">3</text><text x="1040.8" y="390">4</text><text x="1061" y="390">5</text>
        <text x="1081.2" y="390">6</text><text x="1101.4" y="390">7</text><text x="1121.6" y="390">8</text>
        <text x="1141.8" y="390">9</text><text x="1162" y="390">10</text>
        <text x="1034" y="404">Years Since Diagnosis</text>
      </g>
      <polyline points="960,275.4 980.2,283.9 1000.4,275.2 1020.6,278.9 1040.8,265.7 1061,252.3 1081.2,239.2 1101.4,252.3 1121.6,266.8 1141.8,237.6 1162,236.4" fill="none" stroke="var(--peach)" stroke-width="1"/>
      <g fill="var(--peach)">
        <circle cx="960" cy="275.4" r="1.6"/><circle cx="980.2" cy="283.9" r="1.6"/><circle cx="1000.4" cy="275.2" r="1.6"/>
        <circle cx="1020.6" cy="278.9" r="1.6"/><circle cx="1040.8" cy="265.7" r="1.6"/><circle cx="1061" cy="252.3" r="1.6"/>
        <circle cx="1081.2" cy="239.2" r="1.6"/><circle cx="1101.4" cy="252.3" r="1.6"/><circle cx="1121.6" cy="266.8" r="1.6"/>
        <circle cx="1141.8" cy="237.6" r="1.6"/><circle cx="1162" cy="236.4" r="1.6"/>
      </g>
      <polyline points="960,320 980.2,311.9 1000.4,313.3 1020.6,305 1040.8,308.5 1061,304 1081.2,291.6 1101.4,286.3 1121.6,282.4 1141.8,276.9 1162,273.4" fill="none" stroke="var(--lavender)" stroke-width="1"/>
      <g fill="var(--lavender)">
        <circle cx="960" cy="320" r="1.6"/><circle cx="980.2" cy="311.9" r="1.6"/><circle cx="1000.4" cy="313.3" r="1.6"/>
        <circle cx="1020.6" cy="305" r="1.6"/><circle cx="1040.8" cy="308.5" r="1.6"/><circle cx="1061" cy="304" r="1.6"/>
        <circle cx="1081.2" cy="291.6" r="1.6"/><circle cx="1101.4" cy="286.3" r="1.6"/><circle cx="1121.6" cy="282.4" r="1.6"/>
        <circle cx="1141.8" cy="276.9" r="1.6"/><circle cx="1162" cy="273.4" r="1.6"/>
      </g>
      <g class="small" font-size="4.8" text-anchor="middle">
        <text x="962" y="271">961</text><text x="980" y="279">881</text><text x="1001" y="283">963</text>
        <text x="1021" y="274">928</text><text x="1041" y="274">1053</text><text x="1061" y="260">1180</text>
        <text x="1081" y="235">1304</text><text x="1104" y="248">1180</text><text x="1121" y="262">1043</text>
        <text x="1144" y="233">1319</text><text x="1169" y="233">13</text>
        <text x="962" y="328">539</text><text x="982" y="308">616</text><text x="1001" y="321">603</text>
        <text x="1021" y="300">681</text><text x="1041" y="316">648</text><text x="1061" y="312">691</text>
        <text x="1081" y="298">808</text><text x="1101" y="293">858</text><text x="1121" y="290">895</text>
        <text x="1142" y="284">947</text><text x="1169" y="272">97</text>
      </g>
      <line x1="1036" y1="422.5" x2="1054" y2="422.5" stroke="var(--peach)" stroke-width="1"/>
      <circle cx="1045" cy="422.5" r="1.8" fill="var(--peach)"/>
      <text class="small" x="1058" y="424.6" font-size="5.8">LONELY</text>
      <line x1="1088" y1="422.5" x2="1106" y2="422.5" stroke="var(--lavender)" stroke-width="1"/>
      <circle cx="1097" cy="422.5" r="1.8" fill="var(--lavender)"/>
      <text class="small" x="1110" y="424.6" font-size="5.8">NOT LONELY</text>
    </g>

    <!-- footer band -->
    <path d="M0 936 V920 Q0 889 40 889 H1160 Q1200 889 1200 920 V936 Z" fill="var(--blue)"/>
  </svg>

  <!-- findings -->
  <p class="finding finding--summary">PRO-PD scores increased as measures of social health worsend</p>
  <p class="finding finding--side" style="top:454px;height:48px">Overall, individuals identifying as being lonely reported consistently greater PD symptom severity.</p>
  <p class="finding finding--side" style="top:517px;height:79px">Although tremor is a cardinal symptom of PD and highly visible, feeling socially withdrawn is more closely correlated to overall quality of life than tremor.</p>
  <p class="finding finding--side" style="top:657px;height:83px">Individuals who reported feeling lonely reported greater overall PD symptom severity (+328; p=0.000), which was even higher than scores for smoking tobacco (+180; p=0.000).</p>
  <p class="finding finding--side" style="top:758px;height:98px">In contrast individuals that reported having a lot of friends had reduced PD severity scores (-168; p=0.000). Notably, exercising 7 days per week was less beneficial (-301; p=0.000) than feeling lonely was detrimental.</p>

  <footer class="footer-text">www.MovingWellWithPD.org &nbsp;| &nbsp;2020 R Alder</footer>
</main>
</body>
</html>
```